Working Capital graphics

Our business advisory firm requires 9 images to be re-created and improved in the branding of our business.

The 9 images have been uploaded below and the colours and branding of the business can be found at the website www.tallowmereadvisory.com.au

```html
<!DOCTYPE html>
<html lang="en">
<head>
<meta charset="utf-8">
<title>Next $100 of Sales Volume</title>
<link rel="stylesheet" href="https://fonts.googleapis.com/css2?family=Montserrat:wght@500;600;800&display=swap">
<style>
  :root {
    --bg: #ffffff;
    --ink: #111111;
    --royal: #3a58a8;
    --navy: #233b80;
    --midnight: #1a2350;
    --mist: #e3e4e7;
    --amber: #f09d40;
    --sky: #55a7dc;
    --flag: #e8203a;
    --pole: #a9a9a9;
    --white: #ffffff;
  }
  html, body {
    margin: 0;
    padding: 0;
    width: 1200px;
    height: 1000px;
    overflow: hidden;
    background: var(--bg);
  }
  .cycle {
    display: block;
    width: 1200px;
    height: 1000px;
    font-family: "Montserrat", sans-serif;
  }
  .seg-royal { fill: var(--royal); }
  .seg-mist { fill: var(--mist); }
  .seg-navy { fill: var(--navy); }
  .seg-amber { fill: var(--amber); }
  .seg-sky { fill: var(--sky); }
  .hub-gap { fill: var(--white); }
  .hub { fill: var(--midnight); }
  .hub-title { fill: var(--white); font-weight: 800; font-size: 52px; text-anchor: middle; }
  .seg-label { font-size: 20px; font-weight: 500; text-anchor: middle; }
  .seg-label.light { fill: var(--white); }
  .seg-label.dark { fill: var(--ink); }
  .milestone { fill: var(--ink); font-size: 20px; font-weight: 600; text-anchor: middle; }
  .flag-cloth { fill: var(--flag); }
  .flag-pole { stroke: var(--pole); stroke-width: 4; stroke-linecap: round; }
</style>
</head>
<body>
<svg class="cycle" viewBox="0 0 1200 1000" xmlns="http://www.w3.org/2000/svg">
  <defs>
    <g id="marker-flag">
      <line class="flag-pole" x1="0" y1="0" x2="12" y2="54"/>
      <path class="flag-cloth" d="M0,2 C12,-6 24,8 40,0 L44,18 C30,26 18,12 4,20 Z"/>
    </g>
  </defs>

  <g class="ring">
    <path class="seg-mist" d="M693.9,84 A397,397 0 0 1 950.2,247.3 L908.3,330.6 L821.6,337.3 A240,240 0 0 0 666.7,238.6 L723.3,172.6 Z"/>
    <path class="seg-navy" d="M950.2,247.3 A397,397 0 0 1 961.7,685.4 L868.6,679.4 L828.5,602.2 A240,240 0 0 0 821.6,337.3 L908.3,330.6 Z"/>
    <path class="seg-amber" d="M961.7,685.4 A397,397 0 0 1 659.6,870.5 L608.4,792.6 L645.9,714.1 A240,240 0 0 0 828.5,602.2 L868.6,679.4 Z"/>
    <path class="seg-sky" d="M659.6,870.5 A397,397 0 0 1 288.3,685.4 L334.5,604.3 L421.5,602.2 A240,240 0 0 0 645.9,714.1 L608.4,792.6 Z"/>
    <path class="seg-amber" d="M288.3,685.4 A397,397 0 0 1 288.3,264.6 L381.4,270.6 L421.5,347.8 A240,240 0 0 0 421.5,602.2 L334.5,604.3 Z"/>
    <path class="seg-sky" d="M288.3,264.6 A397,397 0 0 1 432.5,127.8 L511,178.1 L508.6,265.1 A240,240 0 0 0 421.5,347.8 L381.4,270.6 Z"/>
    <path class="seg-royal" d="M432.5,127.8 A397,397 0 0 1 693.9,84 L723.3,172.6 L666.7,238.6 A240,240 0 0 0 508.6,265.1 L511,178.1 Z"/>
  </g>

  <circle class="hub-gap" cx="625" cy="475" r="240"/>
  <circle class="hub" cx="625" cy="475" r="217"/>
  <text class="hub-title" x="625" y="460">Next $100 of</text>
  <text class="hub-title" x="625" y="525">Sales Volume</text>

  <g class="segment-labels">
    <text class="seg-label light" x="577" y="164">$0</text>
    <text class="seg-label dark" x="780" y="211">Cost of Sales</text>
    <text class="seg-label light" x="939" y="420">Operating</text>
    <text class="seg-label light" x="939" y="448">Expenses</text>
    <text class="seg-label light" x="933" y="565">Fixed</text>
    <text class="seg-label light" x="933" y="593">Costs</text>
    <text class="seg-label dark" x="846" y="710">Tax</text>
    <text class="seg-label dark" x="782" y="764">Interest</text>
    <text class="seg-label dark" x="694" y="809">Dividends</text>
    <text class="seg-label light" x="375" y="672">AR</text>
    <text class="seg-label light" x="375" y="700">Days</text>
    <text class="seg-label light" x="448" y="746">AP</text>
    <text class="seg-label light" x="448" y="774">Days</text>
    <text class="seg-label light" x="550" y="789">Inv</text>
    <text class="seg-label light" x="550" y="817">Days</text>
    <text class="seg-label light" x="303" y="455">Additional</text>
    <text class="seg-label light" x="303" y="483">Debt</text>
    <text class="seg-label light" x="432" y="213">Cash</text>
    <text class="seg-label light" x="432" y="241">Shortfall</text>
  </g>

  <g class="milestones">
    <text class="milestone" x="615" y="57">Revenue $0</text>

    <use href="#marker-flag" x="1090" y="232"/>
    <text class="milestone" x="1043" y="247">Gross</text>
    <text class="milestone" x="1043" y="275">Margin</text>
    <text class="milestone" x="1043" y="303">$0</text>

    <use href="#marker-flag" x="1082" y="656"/>
    <text class="milestone" x="1035" y="688">EBIT</text>
    <text class="milestone" x="1035" y="716">$0</text>

    <use href="#marker-flag" x="540" y="898"/>
    <text class="milestone" x="647" y="921">Retained</text>
    <text class="milestone" x="647" y="949">Income $0</text>

    <use href="#marker-flag" x="70" y="660"/>
    <text class="milestone" x="172" y="649">After</text>
    <text class="milestone" x="172" y="677">Working</text>
    <text class="milestone" x="172" y="705">Capital</text>
    <text class="milestone" x="172" y="733">$0</text>

    <use href="#marker-flag" x="70" y="235"/>
    <text class="milestone" x="172" y="228">After</text>
    <text class="milestone" x="172" y="256">Additional</text>
    <text class="milestone" x="172" y="284">Funding</text>
    <text class="milestone" x="172" y="312">$0</text>
  </g>
</svg>
</body>
</html>
```